Automotive component supplier needs a business card design

We need a business card design for our company called Velran Global Components Ltd based in the UK. We are a supplier of interior and exterior components to premium car manufacturers such as Corvel Ashby, Hadley Fenn, Marquist and Tavarelli. We would like to see a modern business card design that uses the colour blue.

Target Market(s)

Premium automotive car manufacturers.

Industry/Entity Type

Automotive

Contact Information for Business Card

Company Name : Velran Global Components Limited
Address: 17 Marlow Yard, Upper Heath, Warwick, CV31 8QL, United Kingdom
Web Address : www.velrancomponents-example.co.uk

Font styles to use
Other font styles liked:
• Helvetica

Colors
3176b5
0255a3
85acd3
cfdeed
cee9f5
85cae6
34a6d7
0692cd
9bcb3c

Requirements
Must have
• Clear company logo and a mixture of blue colours.
Nice to have
• A high quality modern image.
Should not have
• Multiple colours.

```html
<!DOCTYPE html>
<html lang="en">
<head>
<meta charset="utf-8">
<title>Velran Global Components – Business Card</title>
<link rel="stylesheet" href="https://fonts.googleapis.com/css2?family=Lato:wght@400;700;900&display=swap">
<style>
  :root {
    --backdrop: #3b3d40;
    --brand-blue: #0a87cc;
    --deep-blue: #0255a3;
    --accent-green: #9bcb3c;
    --paper: #ffffff;
    --ink: #1f2a33;
  }
  * { margin: 0; padding: 0; box-sizing: border-box; }
  html, body {
    width: 1200px; height: 800px; overflow: hidden;
    background: var(--backdrop);
    font-family: "Lato", Helvetica, Arial, sans-serif;
  }
  .stage {
    position: relative; width: 1200px; height: 800px;
    display: flex; align-items: center; justify-content: center; gap: 40px;
  }
  .card {
    position: relative; width: 540px; height: 324px; overflow: hidden;
    box-shadow: 0 10px 30px rgba(0,0,0,.35);
  }
  .card--front { background: var(--brand-blue); color: var(--paper); }
  .card--back { background: var(--paper); color: var(--ink); }

  .wordmark { font-weight: 900; letter-spacing: .5px; line-height: 1.05; white-space: nowrap; }

  .card--front .wordmark {
    position: absolute; left: 0; right: 0; top: 110px; text-align: center;
    font-size: 38px; color: var(--paper);
  }
  .card--front .site {
    position: absolute; left: 0; right: 0; bottom: 40px; text-align: center;
    font-size: 15px; letter-spacing: 1px;
  }

  .card__swoosh { position: absolute; inset: 0; width: 100%; height: 100%; }

  .card--back .wordmark {
    position: absolute; right: 30px; top: 34px; font-size: 24px; color: var(--brand-blue);
  }
  .person { position: absolute; left: 330px; top: 118px; }
  .person__name { font-size: 21px; font-weight: 700; color: var(--brand-blue); }
  .person__role { font-size: 14px; color: var(--ink); margin-top: 2px; }

  .address { position: absolute; left: 30px; top: 168px; font-size: 14px; line-height: 1.35; font-style: normal; }
  .contacts { position: absolute; left: 30px; top: 232px; list-style: none; font-size: 14px; line-height: 1.4; }
  .contacts li { display: flex; align-items: center; gap: 9px; }
  .contacts svg { width: 12px; height: 12px; fill: var(--brand-blue); flex: none; }
</style>
</head>
<body>
<main class="stage">

  <section class="card card--front" aria-label="Business card front">
    <p class="wordmark">Velran Global Components</p>
    <p class="site">www.velrancomponents-example.co.uk</p>
  </section>

  <section class="card card--back" aria-label="Business card back">
    <svg class="card__swoosh" viewBox="0 0 540 324" preserveAspectRatio="none" aria-hidden="true">
      <path d="M0 0 H170 Q60 40 0 120 Z" fill="var(--brand-blue)"/>
      <path d="M0 120 Q60 40 170 0 H190 Q80 50 0 150 Z" fill="var(--accent-green)"/>
      <path d="M540 150 Q480 250 330 324 H540 Z" fill="var(--brand-blue)"/>
      <path d="M540 140 Q475 250 300 324 H322 Q470 255 540 158 Z" fill="var(--accent-green)"/>
    </svg>

    <p class="wordmark">Velran Global Components</p>

    <div class="person">
      <p class="person__name">Marten Holloway</p>
      <p class="person__role">Manager</p>
    </div>

    <address class="address">
      17 Marlow Yard, Upper Heath<br>
      Warwick, CV31 8QL<br>
      United Kingdom
    </address>

    <ul class="contacts">
      <li><svg viewBox="0 0 12 12"><path d="M2.5 0.5 L4.5 0.5 L5.2 3 L3.8 4.2 Q5 6.8 7.8 8.2 L9 6.8 L11.5 7.5 L11.5 9.5 Q11 11.5 9 11.5 Q1 10.5 0.5 3 Q0.5 1 2.5 0.5 Z"/></svg>512 004 7300</li>
      <li><svg viewBox="0 0 12 12"><path d="M3 0 H9 Q10 0 10 1 V11 Q10 12 9 12 H3 Q2 12 2 11 V1 Q2 0 3 0 Z M3.2 1.5 V9.5 H8.8 V1.5 Z"/></svg>512 004 7301</li>
      <li><svg viewBox="0 0 12 12"><path d="M0 2 H12 V10 H0 Z M0.8 2.6 L6 6.6 L11.2 2.6 V3.6 L6 7.6 L0.8 3.6 Z" fill-rule="evenodd"/></svg>info@velrancomponents-example.co.uk</li>
      <li><svg viewBox="0 0 12 12"><circle cx="6" cy="6" r="5.5"/><path d="M0.5 6 H11.5 M6 0.5 V11.5 M2 3 H10 M2 9 H10" stroke="#fff" stroke-width=".7" fill="none"/></svg>www.velrancomponents-example.co.uk</li>
    </ul>
  </section>

</main>
</body>
</html>
```